Webdesign für Projektmanagement
Zielgruppe
Projektmanagement und Projektsteuerung von Bauvorhaben für Projektentwickler und Bauträger.
Wesentliche Bereiche sind Wirtschaftliche Steuerung, Steuerung der Baustelle und Bauabläufe sowie Steuerung der Marketing und Vertriebsaktivitäten.
Aufgabenstellung
Orientierung am Logo. Logo und Visitenkarte liegen bei. Schriftart Prelo und Prelo Slab.

```html
<!DOCTYPE html>
<html lang="de">
<head>
<meta charset="utf-8">
<title>Halvorn Real Estate – Projektmanagement</title>
<link rel="stylesheet" href="https://fonts.googleapis.com/css2?family=Raleway:ital,wght@0,300;0,400;0,500;0,600;0,700;1,300;1,400&display=swap">
<style>
  :root{
    --navy:#03243d;
    --navy-deep:#021d33;
    --gold:#a48d4c;
    --white:#ffffff;
    --card:#f1f1f1;
    --text:#3a3a3a;
    --muted:#6b6b6b;
    --line:#ececec;
    --hero-a:#2a3847;
    --hero-b:#1a2636;
  }
  *{margin:0;padding:0;box-sizing:border-box}
  html,body{width:1036px;height:1200px;overflow:hidden;background:var(--navy);font-family:"Raleway",sans-serif}
  .site{position:absolute;left:0;top:301px;width:1036px;height:597px;display:flex;box-shadow:0 10px 40px rgba(0,0,0,.4)}
  .sidebar{width:159px;height:100%;background:var(--white);position:relative}
  .brand{position:absolute;left:24px;top:56px;color:var(--navy);font-weight:700;line-height:1}
  .brand-name{font-size:21px;letter-spacing:-.3px;display:block}
  .brand-sub{font-size:10px;display:block;text-align:right;margin-top:2px}
  .nav{position:absolute;top:146px;left:0;right:0;list-style:none;border-top:1px solid var(--line)}
  .nav li{height:32px;border-bottom:1px solid var(--line);display:flex;align-items:center;padding:0 17px 0 24px;font-size:9px;color:var(--navy);letter-spacing:.2px;justify-content:space-between}
  .nav li.active{color:var(--gold);font-weight:600}
  .nav .chev{color:var(--gold);font-size:9px}
  .nav .search{color:#9a9a9a;font-style:italic;justify-content:flex-start;gap:7px}
  .social{position:absolute;bottom:22px;left:34px;display:flex;gap:11px}
  .social span{width:9px;height:9px;border-radius:50%;background:var(--navy);display:block}
  .main{flex:1;position:relative;overflow:hidden}
  .hero-photo{position:absolute;inset:0;background:radial-gradient(ellipse at 30% 35%,#3a4a5b 0%,transparent 55%),radial-gradient(ellipse at 85% 60%,#34424f 0%,transparent 50%),linear-gradient(180deg,var(--hero-a),var(--hero-b))}
  .topbar{position:absolute;left:0;right:0;top:0;height:30px;background:rgba(255,255,255,.1);display:flex;align-items:center;padding-left:55px;gap:18px;color:var(--white);font-size:8.5px}
  .topbar .item{display:flex;align-items:center;gap:6px}
  .topbar svg{width:9px;height:9px}
  .hero{position:absolute;left:55px;top:186px;color:var(--white)}
  .hero .kicker{color:var(--gold);font-weight:700;font-size:15.5px;letter-spacing:.2px}
  .hero h1{font-weight:300;font-size:46px;line-height:58px;letter-spacing:.5px;margin-top:6px}
  .cards{position:absolute;left:55px;top:372px;display:flex;gap:9px}
  .card{width:244px;height:146px;background:var(--card);position:relative;padding:10px 12px}
  .card .cat{font-style:italic;font-weight:300;font-size:8.5px;color:var(--muted)}
  .card h2{color:var(--gold);font-weight:500;font-size:10px;line-height:13.5px;margin-top:8px}
  .card p{color:var(--text);font-size:8.5px;line-height:13.5px;margin-top:7px;font-weight:400}
  .card .more{position:absolute;right:0;bottom:0;background:var(--navy);color:var(--white);font-size:7.5px;font-weight:600;letter-spacing:.3px;padding:7px 12px}
  .footer{position:absolute;left:0;right:0;bottom:0;height:36px;background:rgba(0,0,0,.12);padding-left:55px;display:flex;align-items:center;font-size:8.5px;color:rgba(255,255,255,.12)}
</style>
</head>
<body>
<div class="site">
  <aside class="sidebar">
    <div class="brand"><span class="brand-name">Halvorn</span><span class="brand-sub">Real Estate</span></div>
    <ul class="nav">
      <li class="active">HOME</li>
      <li>LEISTUNGEN</li>
      <li>ÜBER UNS <span class="chev">›</span></li>
      <li>PROJEKTE <span class="chev">›</span></li>
      <li>PARTNER</li>
      <li>KONTAKT</li>
      <li class="search"><svg width="8" height="8" viewBox="0 0 10 10"><circle cx="4" cy="4" r="3" fill="none" stroke="#a48d4c" stroke-width="1.4"/><line x1="6.3" y1="6.3" x2="9" y2="9" stroke="#a48d4c" stroke-width="1.6"/></svg>Suchen</li>
    </ul>
    <div class="social" aria-label="Soziale Netzwerke"><span></span><span></span><span></span><span></span></div>
  </aside>
  <main class="main">
    <div class="hero-photo" role="img" aria-label="Abgedunkeltes Foto: Bauhelm, Baupläne und Brille auf einem Schreibtisch"></div>
    <div class="topbar">
      <div class="item"><svg viewBox="0 0 10 10"><path d="M2 1l2 2-1 1.3c.6 1.2 1.5 2.1 2.7 2.7L7 6l2 2-1.3 1.3C4.5 9 1 5.5.7 2.3z" fill="#5f88b5"/></svg>+49 (0)123 - 456 789 00</div>
      <div class="item"><svg viewBox="0 0 10 10"><circle cx="5" cy="5" r="4" fill="none" stroke="#5f88b5" stroke-width="1.1"/><path d="M5 2.6V5h2" fill="none" stroke="#5f88b5" stroke-width="1.1"/></svg>Mo - Fr 9:00 - 18:00</div>
      <div class="item"><svg viewBox="0 0 10 10"><rect x=".5" y="2" width="9" height="6" fill="#5f88b5"/><path d="M.5 2L5 5.5 9.5 2" fill="none" stroke="#2a3847" stroke-width=".8"/></svg>info@halvorn-re.de</div>
      <div class="item"><svg viewBox="0 0 10 10"><path d="M5 .5a3.2 3.2 0 0 1 3.2 3.2C8.2 6 5 9.5 5 9.5S1.8 6 1.8 3.7A3.2 3.2 0 0 1 5 .5z" fill="#5f88b5"/><circle cx="5" cy="3.7" r="1.1" fill="#2a3847"/></svg>Lindenallee 14, 40210 Musterstadt</div>
    </div>
    <section class="hero">
      <div class="kicker">PROJEKTMANAGEMENT &amp; PROJEKTSTEUERUNG</div>
      <h1>WIR REALISIEREN<br>BAUVORHABEN</h1>
    </section>
    <section class="cards">
      <article class="card">
        <div class="cat">Betriebswirtschaftliche Planung</div>
        <h2>STET CLITA KASD GUBERGREN NO SEA<br>TAKIMATA SANCTUS EST LOREM IPSUM</h2>
        <p>Lorem ipsum dolor sit amet, consetetur sadipscing elitr, sed diam nonumy eirmod tempor invidunt ut labore et dolore magna aliquyam erat, sed diam voluptua.</p>
        <div class="more">WEITERLESEN</div>
      </article>
      <article class="card">
        <div class="cat">Steuerung der baulichen Umsetzung</div>
        <h2>STET CLITA KASD GUBERGREN NO SEA<br>TAKIMATA SANCTUS EST LOREM IPSUM</h2>
        <p>Lorem ipsum dolor sit amet, consetetur sadipscing elitr, sed diam nonumy eirmod tempor invidunt ut labore et dolore magna aliquyam erat, sed diam voluptua.</p>
        <div class="more">WEITERLESEN</div>
      </article>
      <article class="card">
        <div class="cat">Marketing und Vertrieb</div>
        <h2>STET CLITA KASD GUBERGREN NO SEA<br>TAKIMATA SANCTUS EST LOREM IPSUM</h2>
        <p>Lorem ipsum dolor sit amet, consetetur sadipscing elitr, sed diam nonumy eirmod tempor invidunt ut labore et dolore magna aliquyam erat, sed diam voluptua.</p>
        <div class="more">WEITERLESEN</div>
      </article>
    </section>
    <footer class="footer">© 2017 Halvorn Real Estate GmbH - Impressum</footer>
  </main>
</div>
</body>
</html>
```